RK Donnelly & Associates

Create a website encompassing design work already carried out for business card.
Small accounting practice, business accounting and management, superannuation, audit, taxation.

```html
<!DOCTYPE html>
<html lang="en">
<head>
<meta charset="utf-8">
<title>RK Donnelly &amp; Associates</title>
<link rel="stylesheet" href="https://fonts.googleapis.com/css2?family=Open+Sans:wght@400;600;700&family=Roboto+Slab:wght@400&display=swap">
<style>
:root{
  --ink:#1e1e1e;
  --header:#1d1d1d;
  --blue:#6ea6db;
  --blue-mid:#4e88c7;
  --blue-deep:#0f4a80;
  --link:#2f74c0;
  --heading:#333;
  --text:#777;
  --grey-band:#e6e6e6;
  --footer:#2f353d;
  --footer-base:#22262b;
  --footer-text:#8a9098;
  --white:#fff;
  --line:#dcdcdc;
}
*{margin:0;padding:0;box-sizing:border-box}
html,body{width:1200px;height:2250px;overflow:hidden}
body{position:relative;background:var(--white);font-family:"Open Sans",Arial,sans-serif;color:var(--text)}
.abs{position:absolute}

/* header */
.site-header{left:0;top:0;width:1200px;height:127px;background:var(--header)}
.nav a{position:absolute;top:50px;color:var(--white);font-size:14px;text-decoration:none;line-height:32px}
.nav .active{border:1px solid var(--blue);padding:0 20px;color:var(--blue)}
.brand{left:474px;top:36px;display:flex;align-items:center;gap:12px}
.brand-square{width:40px;height:40px;background:var(--blue)}
.brand-name{color:var(--white);font-size:22px;font-weight:700;line-height:24px;width:170px}
.service-strip{left:0;top:127px;width:1200px;height:30px;background:var(--blue);color:var(--white);font-size:11px;font-weight:600;text-align:center;line-height:30px}

/* hero */
.hero{left:0;top:157px;width:1200px;height:479px;background:linear-gradient(100deg,#e9e6e1 0%,#cfc9c0 30%,#5d6a82 55%,#2d3d5e 80%,#3a4a6a 100%)}
.hero-arrow{top:228px;width:28px;height:28px}
.hero-title{left:133px;top:320px;height:40px;padding:0 22px;background:var(--blue);color:var(--white);font-size:23px;line-height:40px;font-weight:600;white-space:nowrap}
.hero-sub{left:133px;top:366px;height:40px;padding:0 18px;background:rgba(30,30,30,.85);color:var(--white);font-size:19px;line-height:40px;font-weight:600;white-space:nowrap}

/* services */
.service{top:698px;width:200px}
.service-icon{width:44px;height:44px;background:var(--blue);position:relative}
.service-icon::after{content:"";position:absolute;left:16px;bottom:-7px;border:6px solid transparent;border-top-color:var(--blue);border-bottom:0}
.service-icon svg{position:absolute;left:11px;top:11px}
.service-title{position:absolute;left:58px;top:12px;font-size:16px;color:var(--heading);white-space:nowrap}
.service-text{margin-top:24px;font-size:10px;line-height:16px;color:#888;width:195px}
.service-more{margin-top:20px;font-size:10px;color:var(--link);display:flex;align-items:center;gap:3px}

/* welcome */
.welcome{left:0;top:872px;width:1200px;height:248px;background:var(--grey-band);text-align:center}
.welcome h2{font-weight:400;font-size:29px;color:var(--heading);margin-top:44px}
.welcome h2 span,.section-title span{color:var(--blue-deep)}
.welcome p{width:960px;margin:14px auto 0;font-size:11.5px;line-height:18px;color:#666}
.btn-read{display:inline-block;margin-top:16px;width:162px;height:33px;line-height:33px;background:var(--blue);color:var(--white);font-size:12px;font-weight:600}

/* testimonials */
.section-title{font-weight:400;font-size:29px;color:var(--heading)}
.slider-dot{top:1180px;width:20px;height:20px;border-radius:50%}
.testimonial{top:1225px;width:380px}
.avatar{width:68px;height:68px;border-radius:50%;border:2px solid #ddd;background:linear-gradient(#e4e8ee,#b9c3d1)}
.quote{position:absolute;left:100px;top:10px;width:200px;font-family:"Roboto Slab",Georgia,serif;font-size:12px;line-height:17px;color:#222;text-align:justify}
.quote-mark{float:left;width:36px;height:30px;margin-right:4px}
.person{position:absolute;left:100px;top:92px;font-family:"Roboto Slab",Georgia,serif;font-size:12px;color:#222}
.role{position:absolute;left:100px;top:112px;font-size:8.5px;color:#999}
.role span{color:var(--link)}
.divider{left:70px;top:1398px;width:1058px;height:1px;background:var(--line)}

/* clients */
.client{top:1512px;width:148px;height:88px;border:1px solid #ddd;display:flex;align-items:center;justify-content:center;gap:6px;font-size:13px;font-weight:600;color:#4a6f96}
.client i{width:12px;height:12px;background:#e8833a;display:block}

/* cta */
.cta{left:0;top:1697px;width:1200px;height:73px;background:var(--blue-mid)}
.cta-text{left:110px;top:21px;color:var(--white);font-size:22px;white-space:nowrap}
.cta-btn{left:689px;top:17px;width:372px;height:42px;background:var(--blue-deep);border:1px solid #0a3560;color:var(--white);font-size:20px;font-weight:600;text-align:center;line-height:40px}

/* footer */
.footer{left:0;top:1770px;width:1200px;height:410px;background:var(--footer)}
.footer h4{position:absolute;top:56px;color:var(--white);font-weight:400;font-size:17px}
.footer-list{position:absolute;top:104px;font-size:15px;line-height:20px;color:var(--footer-text);list-style:none}
.mail-link{position:absolute;left:92px;top:228px;color:#b5bbc2;font-size:15px;border-bottom:1px solid #7a828b;line-height:18px}
.newsletter-note{position:absolute;left:798px;top:100px;width:320px;font-size:15px;line-height:20px;color:var(--footer-text)}
.field{position:absolute;left:800px;width:302px;height:48px;background:var(--white);border-radius:2px;padding-left:26px;font-size:15px;line-height:48px;color:#999}
.submit{position:absolute;left:981px;top:301px;width:122px;height:43px;background:var(--blue-mid);color:var(--white);text-align:center;line-height:43px;font-size:14px;font-weight:600}
.footer-base{left:0;top:2180px;width:1200px;height:70px;background:var(--footer-base)}
.copyright{left:70px;top:24px;font-size:15px;color:var(--footer-text)}
.social{top:23px;width:24px;height:24px;border-radius:50%;background:var(--white)}
</style>
</head>
<body>

<header class="site-header abs">
  <nav class="nav">
    <a class="active" style="left:133px">Home</a>
    <a style="left:253px">About Us</a>
    <a style="left:373px">Service</a>
    <a style="left:789px">Blog</a>
    <a style="left:879px">Testimonials</a>
    <a style="left:1021px">Contact</a>
  </nav>
  <div class="brand abs"><span class="brand-square"></span><span class="brand-name">RK Donnelly &amp; Associates.</span></div>
</header>
<div class="service-strip abs">Accountant · Business Solutions · Management · Superannuation · Audit</div>

<section class="hero abs" role="img" aria-label="Photo of two business people reviewing documents at a desk with a laptop">
  <svg class="hero-arrow abs" style="left:31px" viewBox="0 0 28 28"><circle cx="14" cy="14" r="12" fill="none" stroke="#333" stroke-width="2"/><path d="M19 14H9M13 9l-5 5 5 5" fill="none" stroke="#333" stroke-width="2"/></svg>
  <svg class="hero-arrow abs" style="left:1138px" viewBox="0 0 28 28"><circle cx="14" cy="14" r="12" fill="none" stroke="#222" stroke-width="2"/><path d="M9 14h10M15 9l5 5-5 5" fill="none" stroke="#222" stroke-width="2"/></svg>
  <div class="hero-title abs">RK Donnelly &amp; Associates</div>
  <div class="hero-sub abs">Lorem ipsum dolor sit amit contantry opo</div>
</section>

<section class="services">
  <div class="service abs" style="left:70px">
    <div class="service-icon"><svg width="22" height="22" viewBox="0 0 22 22"><rect x="3" y="1" width="14" height="19" fill="none" stroke="#fff" stroke-width="2"/><path d="M6 7h8M6 11h6" stroke="#fff" stroke-width="2"/></svg></div>
    <div class="service-title">Accountant</div>
    <p class="service-text">Vestibulum ante ipsum primis in faucibus orci luctus et ultrices posuere cubilia.</p>
    <div class="service-more">Details <svg width="9" height="9" viewBox="0 0 9 9"><circle cx="4.5" cy="4.5" r="4.5" fill="#2f74c0"/><path d="M3.5 2.5l2 2-2 2" fill="none" stroke="#fff"/></svg></div>
  </div>
  <div class="service abs" style="left:295px">
    <div class="service-icon"><svg width="22" height="22" viewBox="0 0 22 22"><circle cx="11" cy="6" r="4" fill="#fff"/><path d="M3 21c0-6 4-9 8-9s8 3 8 9z" fill="#fff"/></svg></div>
    <div class="service-title">Business Solution</div>
    <p class="service-text">Suspendisse in sapien auctor sapien vulputate porttitor. Integer lacinia.</p>
    <div class="service-more">Details <svg width="9" height="9" viewBox="0 0 9 9"><circle cx="4.5" cy="4.5" r="4.5" fill="#2f74c0"/><path d="M3.5 2.5l2 2-2 2" fill="none" stroke="#fff"/></svg></div>
  </div>
  <div class="service abs" style="left:502px">
    <div class="service-icon"><svg width="22" height="22" viewBox="0 0 22 22"><rect x="2" y="3" width="18" height="13" fill="none" stroke="#fff" stroke-width="2"/><path d="M5 12l4-4 3 3 5-5M11 16v4M7 20h8" fill="none" stroke="#fff" stroke-width="2"/></svg></div>
    <div class="service-title">Management</div>
    <p class="service-text">Etiam in tincidunt arcu, at tempor magna. Maecenas ut odio nunc.</p>
    <div class="service-more">Details <svg width="9" height="9" viewBox="0 0 9 9"><circle cx="4.5" cy="4.5" r="4.5" fill="#2f74c0"/><path d="M3.5 2.5l2 2-2 2" fill="none" stroke="#fff"/></svg></div>
  </div>
  <div class="service abs" style="left:725px">
    <div class="service-icon"><svg width="22" height="22" viewBox="0 0 22 22"><path d="M10 3a9 9 0 1 0 9 9h-9z" fill="#fff"/><path d="M12 1v9h9a9 9 0 0 0-9-9z" fill="#fff"/></svg></div>
    <div class="service-title">Superannuation</div>
    <p class="service-text">Aliquam convallis vitae metus ut luctus. Nulla vestibulum consequat.</p>
    <div class="service-more">Details <svg width="9" height="9" viewBox="0 0 9 9"><circle cx="4.5" cy="4.5" r="4.5" fill="#2f74c0"/><path d="M3.5 2.5l2 2-2 2" fill="none" stroke="#fff"/></svg></div>
  </div>
  <div class="service abs" style="left:942px">
    <div class="service-icon"><svg width="22" height="22" viewBox="0 0 22 22"><circle cx="9" cy="9" r="6" fill="none" stroke="#fff" stroke-width="2.5"/><path d="M13.5 13.5l6 6" stroke="#fff" stroke-width="3"/></svg></div>
    <div class="service-title">Audit</div>
    <p class="service-text">Aliquam convallis vitae metus ut luctus. Nulla vestibulum consequat.</p>
    <div class="service-more">Details <svg width="9" height="9" viewBox="0 0 9 9"><circle cx="4.5" cy="4.5" r="4.5" fill="#2f74c0"/><path d="M3.5 2.5l2 2-2 2" fill="none" stroke="#fff"/></svg></div>
  </div>
</section>

<section class="welcome abs">
  <h2>Welcome To <span>RK Donnelly &amp; Associates</span></h2>
  <p>Lorem ipsum dolor sit amet, consectetur adipiscing elit. Donec nec massa commodo, suscipit justo eu, varius justo. Praesent efficitur mauris erat, ac varius purus sollicitudin a. Praesent semper a libero et pharetra. In massa purus, tempor eget nibh sit amet, hendrerit iaculis lectus. Phasellus sed mauris et est viverra euismod. Suspendisse potenti. Suspendisse vestibulum in nibh id luctus.</p>
  <span class="btn-read">Read More</span>
</section>

<h2 class="section-title abs" style="left:70px;top:1170px">Client <span>Testimonials</span></h2>
<span class="slider-dot abs" style="left:1078px;background:#ccc"></span>
<span class="slider-dot abs" style="left:1106px;background:var(--link)"></span>
<svg class="abs" style="left:1078px;top:1180px" width="48" height="20" viewBox="0 0 48 20"><path d="M12 6l-4 4 4 4M34 6l4 4-4 4" fill="none" stroke="#fff" stroke-width="2"/></svg>

<div class="testimonial abs" style="left:72px">
  <div class="avatar" role="img" aria-label="Portrait photo of the client"></div>
  <div class="quote"><svg class="quote-mark" viewBox="0 0 36 30"><path d="M2 30V14L10 2h5L10 14h6v16zM20 30V14L28 2h5l-5 12h6v16z" fill="#ddd"/></svg>Pellentesque et pulvinar enim. Quisque at tempor ligula. Donec ut purus sed tortor malesuada.</div>
  <div class="person">Dana Whitford</div>
  <div class="role">Art Director / <span>lorem ipsum</span></div>
</div>
<div class="testimonial abs" style="left:452px">
  <div class="avatar" role="img" aria-label="Portrait photo of the client"></div>
  <div class="quote"><svg class="quote-mark" viewBox="0 0 36 30"><path d="M2 30V14L10 2h5L10 14h6v16zM20 30V14L28 2h5l-5 12h6v16z" fill="#ddd"/></svg>Pellentesque et pulvinar enim. Quisque at tempor ligula. Donec ut purus sed tortor malesuada.</div>
  <div class="person">Dana Whitford</div>
  <div class="role">Art Director / <span>lorem ipsum</span></div>
</div>
<div class="testimonial abs" style="left:832px">
  <div class="avatar" role="img" aria-label="Portrait photo of the client"></div>
  <div class="quote"><svg class="quote-mark" viewBox="0 0 36 30"><path d="M2 30V14L10 2h5L10 14h6v16zM20 30V14L28 2h5l-5 12h6v16z" fill="#ddd"/></svg>Pellentesque et pulvinar enim. Quisque at tempor ligula. Donec ut purus sed tortor malesuada.</div>
  <div class="person">Dana Whitford</div>
  <div class="role">Art Director / <span>lorem ipsum</span></div>
</div>
<div class="divider abs"></div>

<h2 class="section-title abs" style="left:0;width:1200px;text-align:center;top:1443px">Our <span>Clients</span></h2>
<div class="client abs" style="left:66px"><i></i>Northfield</div>
<div class="client abs" style="left:249px">Brightway</div>
<div class="client abs" style="left:432px">Fennick</div>
<div class="client abs" style="left:615px">Lumen Co</div>
<div class="client abs" style="left:798px">Arcline</div>
<div class="client abs" style="left:981px">Towerly</div>

<section class="cta abs">
  <div class="cta-text abs">Create your account today. No credit card required.</div>
  <div class="cta-btn abs">Get Started with RK Donnelly</div>
</section>

<footer class="footer abs">
  <h4 style="left:92px">Contact us</h4>
  <ul class="footer-list" style="left:92px"><li>Lorem Ipsum</li><li>2040 Westhaven</li><li>Norland</li><li>&nbsp;</li><li>+ 45 - So Call me Maybe</li></ul>
  <span class="mail-link">Send us an e-mail</span>
  <h4 style="left:385px">Navigation</h4>
  <ul class="footer-list" style="left:385px"><li>- Home</li><li>- Cases</li><li>- About</li><li>- Method</li><li>- Contact</li><li>- Blog</li></ul>
  <h4 style="left:606px">Useful links</h4>
  <ul class="footer-list" style="left:606px"><li>- Home</li><li>- Cases</li><li>- About</li><li>- Method</li><li>- Contact</li><li>- Blog</li></ul>
  <h4 style="left:798px">Submit to our news letter</h4>
  <p class="newsletter-note">Submit and get all the info about our work, new positions and new blog inputs.</p>
  <div class="field" style="top:172px">Your Name</div>
  <div class="field" style="top:232px">Your E-mail</div>
  <div class="submit">Submit</div>
</footer>
<div class="footer-base abs">
  <div class="copyright abs">Copyrights © yoursite All rights reserved</div>
  <span class="social abs" style="left:999px"></span>
  <span class="social abs" style="left:1033px"></span>
  <span class="social abs" style="left:1068px"></span>
  <span class="social abs" style="left:1103px"></span>
</div>

</body>
</html>
```